Webdesign Hauskranken- und Tagespflege „Am Lindenhof“
Zielgruppe
Die Hauskranken- und Tagespflege „Am Lindenhof“ in Chemnitz ist ein unabhängiges, privat geführtes Unternehmen im Bereich der ambulanten und teilstationären Kranken- und Seniorenpflege. Seit der Gründung am 1. Mai 2007 stehen wir für eine zuverlässige, individuelle und herzliche Betreuung unserer Klientinnen und Klienten.
Das Team ist ein engagiertes Pflegeteam und auf über 35 qualifizierte Mitarbeiterinnen und Mitarbeiter angewachsen. Gemeinsam setzen wir uns täglich dafür ein, Menschen mit Pflegebedarf eine bestmögliche Versorgung und ein hohes Maß an Lebensqualität zu ermöglichen.
Unsere Firmenphilosophie basiert auf Wertschätzung, Vertrauen und Respekt – sowohl im Umgang mit unseren Klientinnen und Klienten sowie deren Angehörigen als auch innerhalb unseres Teams. Eine persönliche, einfühlsame und fachlich kompetente Betreuung steht für uns an erster Stelle.
Ob Grundpflege oder Behandlungspflege – bei uns sind Sie in guten Händen. Wir begleiten unsere Klientinnen und Klienten mit Fürsorge, Fachkompetenz und Herz und unterstützen sie dabei, ihren Alltag so selbstbestimmt wie möglich zu gestalten.
Gleichzeitig entlasten wir Angehörige, Freunde und Bekannte, indem wir ihnen Sicherheit geben und Freiräume schaffen. So bleibt mehr Zeit für gemeinsame, unbeschwerte Momente mit den Menschen, die ihnen am Herzen liegen.
Unsere Tagespflege bietet Platz für 18 Gäste. Der große Aufenthaltsraum mit offener Küche lädt zum gemütlichen Beisammensein ein. In unserem Ruheraum können sich unsere Gäste bei Bedarf zurückziehen und sich ausruhen, auch Therapien (Logopädie, Ergotherapie, Physiotherapie…) werden darin durchgeführt. Der Aufenthaltsraum ist zum Teil eingerichtet wie eine gemütliche Wohnstube, ihre Einrichtung erinnert an frühere Zeiten. Gemütliche Ruhesessel laden zum Entspannen ein.
Der persönliche Kontakt und das Vertrauen unserer Patientinnen und Patienten bilden dabei st..
Aufgabenstellung
Ziele des Relaunchs:
modernes, freundliches und barrierearmes Design
klare Benutzerführung für Senioren und Angehörige
Hinweis zum Rückrufservice
Notfallnummer dauerhaft sichtbar
schnelle Kontaktaufnahme (Telefon, Rückruf, Kontaktformular)
bessere Auffindbarkeit bei Google (SEO)
Vertrauen durch authentische Bilder, Teamvorstellung und Bewertungen

```html
<!DOCTYPE html>
<html lang="de">
<head>
<meta charset="utf-8">
<title>Hauskranken- und Tagespflege „Am Lindenhof“</title>
<link href="https://fonts.googleapis.com/css2?family=Inter:ital,wght@0,400;0,500;0,600;0,700;1,400&family=Inter+Tight:wght@500;600&display=swap" rel="stylesheet">
<style>
:root{
  --yellow:#fbe31d;
  --yellow-soft:#fff7c2;
  --cream:#fffbe6;
  --sand:#efebdb;
  --navy:#131a24;
  --ink:#1a1d24;
  --text:#4b505a;
  --muted:#8a8f99;
  --line:#e4e2da;
  --white:#ffffff;
  --ice:#eef2f7;
}
*{box-sizing:border-box;margin:0;padding:0}
html,body{width:1200px;height:4685px;overflow:hidden}
body{font-family:"Inter",sans-serif;color:var(--ink);background:var(--white);position:relative}
h1,h2,h3{font-family:"Inter Tight",sans-serif;font-weight:500;letter-spacing:-.5px}
.abs{position:absolute}
section{position:absolute;left:0;width:1200px}
svg.ico{display:block}
.btn{position:absolute;display:flex;align-items:center;justify-content:center;gap:8px;border-radius:22px;font-size:12px;font-weight:600;height:40px}
.btn-yellow{background:var(--yellow);color:var(--ink)}
.btn-outline{border:1.5px solid var(--yellow);color:var(--white)}
.btn-white{background:var(--white);border:1.5px solid var(--line);color:var(--ink)}

/* Hero */
.hero{top:0;height:686px;background:linear-gradient(90deg,#1a1a1c 0%,#2b2620 35%,#5a4a3a 60%,#8b7660 100%)}
.hero-photo{position:absolute;right:0;top:0;width:760px;height:686px;background:radial-gradient(ellipse at 60% 40%,#c8a889 0%,#8e735b 40%,rgba(60,48,38,.0) 80%)}
.hero-shade{position:absolute;inset:0;background:linear-gradient(90deg,rgba(18,18,20,.85) 0%,rgba(18,18,20,.55) 45%,rgba(18,18,20,0) 75%)}
.topbar{position:absolute;top:22px;display:flex;align-items:center;gap:12px;color:var(--white);font-size:12px;line-height:1.3}
.icon-dot{width:26px;height:26px;border-radius:50%;background:var(--yellow);display:flex;align-items:center;justify-content:center}
.nav{position:absolute;left:95px;top:65px;width:1010px;height:52px;background:var(--white);border-radius:26px}
.nav a{position:absolute;top:17px;font-size:12.5px;color:var(--ink);text-decoration:none}
.nav .active{top:9px;left:14px;padding:8px 22px;background:var(--yellow-soft);border-radius:18px}
.brand{position:absolute;left:538px;top:29px;width:124px;height:124px;border-radius:50%;background:var(--white);box-shadow:0 4px 14px rgba(0,0,0,.15);display:flex;align-items:center;justify-content:center;text-align:center;font-size:12px;font-weight:600;color:var(--ink);line-height:1.3}
.hero h1{position:absolute;left:95px;top:218px;font-size:47px;line-height:58px;color:var(--white)}
.hero h1 .hl{color:var(--yellow);text-decoration:underline;text-decoration-thickness:3px;text-underline-offset:6px}
.hero-lead{position:absolute;left:95px;top:356px;width:520px;font-size:12px;line-height:20px;color:#eceae5}
.checks{position:absolute;left:95px;color:var(--white);font-size:14px;display:flex;gap:20px}
.checks span{display:flex;align-items:center;gap:8px}

/* Services */
.services{top:686px;height:456px}
.card{position:absolute;top:85px;width:240px;height:278px;background:var(--white);border-radius:14px;box-shadow:0 12px 30px rgba(20,20,30,.08);padding:0 24px}
.card.outlined{border:1.5px solid #2b2f37}
.card .badge{position:absolute;top:28px;left:24px;width:62px;height:62px;border-radius:50%;background:var(--yellow);display:flex;align-items:center;justify-content:center}
.card h3{position:absolute;top:128px;left:24px;font-size:18px}
.card p{position:absolute;top:165px;left:24px;width:190px;font-size:10.5px;line-height:15px;color:var(--text)}
.card .more{position:absolute;top:320px;top:232px;left:24px;font-size:12px;font-weight:600}

/* Leitbild */
.leitbild{top:1142px;height:549px;background:var(--cream)}
.sec-title{position:absolute;font-size:35px;line-height:44px}
.body-text{position:absolute;font-size:11.5px;line-height:19px;color:var(--text)}
.photo{position:absolute;border-radius:14px}

/* Features */
.feature-box{position:absolute;background:var(--cream);border-radius:12px;padding:16px 18px}
.feature-box h4{font-size:16px;font-weight:500;margin-bottom:14px}
.feature-list{display:grid;grid-template-columns:1fr 1fr;row-gap:12px;font-size:12px;column-gap:10px}
.feature-list span{display:flex;align-items:center;gap:8px}

/* Team */
.team{top:2743px;height:778px;background:var(--navy);color:var(--white);text-align:center}
.team h2{position:absolute;left:0;width:1200px;top:68px;font-size:35px;line-height:44px}
.team .sub{position:absolute;left:0;width:1200px;top:168px;color:var(--yellow);font-size:16px;font-weight:500}
.member{position:absolute;top:235px;width:238px;height:398px;background:var(--white);border-radius:119px 119px 100px 100px;color:var(--ink)}
.member .ring{position:absolute;left:39px;top:22px;width:160px;height:160px;border-radius:50%;background:var(--ice);display:flex;align-items:center;justify-content:center}
.member .pic{width:140px;height:140px;border-radius:50%}
.member .name{position:absolute;top:218px;left:0;width:100%;font-size:17px;font-family:"Inter Tight",sans-serif;font-weight:500}
.member .role{position:absolute;top:244px;left:0;width:100%;font-size:10px;font-style:italic;color:var(--muted)}
.member ul{position:absolute;top:278px;left:20px;width:198px;list-style:none;font-size:10px;line-height:14px;color:var(--muted)}
.member .go{position:absolute;left:105px;top:345px;width:28px;height:28px;border-radius:50%;background:var(--yellow);font-size:12px;display:flex;align-items:center;justify-content:center}

/* Contact */
.contact{top:3521px;height:679px}
.form-box{position:absolute;left:95px;top:89px;width:683px;height:500px;background:var(--sand);border-radius:18px}
.field{position:absolute;background:var(--white);border-radius:26px;font-size:12px;color:var(--muted);padding-left:32px;display:flex;align-items:center}
.hours{position:absolute;left:791px;top:89px;width:333px;height:500px;background:var(--yellow);border-radius:18px;padding:0 31px}
.hours h3{position:absolute;top:26px;left:31px;font-size:25px}
.hours table{position:absolute;top:98px;left:31px;width:260px;border-collapse:collapse;font-size:11px}
.hours td{height:29px;vertical-align:middle}
.hours td+td{width:118px}
.hour-rule{position:absolute;left:31px;top:313px;width:273px;border-top:1px solid rgba(0,0,0,.25)}
.cinfo{position:absolute;display:flex;gap:10px;font-size:11px;line-height:15px}
.cicon{width:28px;height:28px;border-radius:50%;background:var(--ink);display:flex;align-items:center;justify-content:center;flex:none}

/* Footer */
.footer{top:4200px;height:485px}
.foot-mark{position:absolute;left:94px;top:69px;width:240px;height:240px;border-radius:50%;background:var(--ice);display:flex;align-items:center;justify-content:center;text-align:center;font-size:15px;font-weight:600;line-height:1.4;color:var(--ink)}
.vrule{position:absolute;top:69px;height:258px;border-left:1px solid var(--line)}
.foot-col h3{position:absolute;top:62px;font-size:22px;padding-bottom:6px;border-bottom:2px solid var(--yellow)}
.foot-links{position:absolute;left:574px;top:128px;list-style:none;font-size:11.5px;line-height:27px}
.foot-bottom{position:absolute;left:95px;width:1010px;top:418px;border-top:1px solid var(--line)}
.legal{position:absolute;top:440px;font-size:11px;color:var(--text)}
</style>
</head>
<body>

<svg width="0" height="0" style="position:absolute">
  <symbol id="phone" viewBox="0 0 24 24"><path d="M6.6 10.8a15.1 15.1 0 006.6 6.6l2.2-2.2a1 1 0 011-.25 11.4 11.4 0 003.6.6 1 1 0 011 1V20a1 1 0 01-1 1A17 17 0 013 4a1 1 0 011-1h3.5a1 1 0 011 1c0 1.25.2 2.45.6 3.6a1 1 0 01-.25 1z"/></symbol>
  <symbol id="tick" viewBox="0 0 24 24"><circle cx="12" cy="12" r="11" fill="#fbe31d"/><path d="M7 12.5l3.2 3.2L17 9" fill="none" stroke="#1a1d24" stroke-width="2.4" stroke-linecap="round" stroke-linejoin="round"/></symbol>
  <symbol id="mail" viewBox="0 0 24 24"><rect x="3" y="6" width="18" height="12" rx="2" fill="none" stroke="#fff" stroke-width="2"/><path d="M3 7l9 6 9-6" fill="none" stroke="#fff" stroke-width="2"/></symbol>
  <symbol id="pin" viewBox="0 0 24 24"><path d="M12 2a7 7 0 00-7 7c0 5 7 13 7 13s7-8 7-13a7 7 0 00-7-7zm0 9.5A2.5 2.5 0 1112 6.5a2.5 2.5 0 010 5z" fill="#fff"/></symbol>
</svg>

<!-- Hero -->
<section class="hero">
  <div class="hero-photo" role="img" aria-label="Pflegerin umarmt lächelnd eine ältere Dame auf dem Sofa"></div>
  <div class="hero-shade"></div>

  <div class="topbar" style="left:95px">
    <div class="icon-dot"><svg class="ico" width="14" height="14"><use href="#phone"/></svg></div>
    <span>24-hour hotline : <b>0371 / 4470218</b></span>
  </div>
  <div class="topbar" style="left:897px;top:20px">
    <div class="icon-dot"><svg class="ico" width="14" height="14"><use href="#phone"/></svg></div>
    <span>Mon - Thurs: 9:00 am - 3:00 pm<br>Fri: 9:00 am - 2:00 pm</span>
  </div>

  <nav class="nav">
    <a class="active" href="#">Heim</a>
    <a href="#" style="left:127px">Über uns</a>
    <a href="#" style="left:218px">Team</a>
    <a href="#" style="left:292px">Pflegeleitbild</a>
    <a href="#" style="left:607px">Partner</a>
    <a href="#" style="left:676px">Hauskrankenpflege</a>
    <a href="#" style="left:811px">Tagespflege</a>
    <a href="#" style="left:907px">Aktuelles</a>
  </nav>
  <div class="brand">Am<br>Lindenhof</div>

  <h1>Pflege Mit Herz.<br>Für Mehr <span class="hl">Lebensqualität.</span></h1>
  <p class="hero-lead">Seit 2007 bieten wir Menschen in Chemnitz eine zuverlässige, individuelle und herzliche Betreuung – in der eigenen Häuslichkeit und in unserer Tagespflege.</p>

  <a class="btn btn-yellow" style="left:95px;top:412px;width:172px"><svg class="ico" width="13" height="13"><use href="#phone"/></svg>0371 4470218</a>
  <a class="btn btn-outline" style="left:278px;top:412px;width:175px">Rückruf anfordern</a>

  <div class="checks" style="top:489px">
    <span><svg width="17" height="17"><use href="#tick"/></svg>Persönlich &amp; einfühlsam</span>
    <span><svg width="17" height="17"><use href="#tick"/></svg>Kompetent &amp; zuverlässig</span>
  </div>
  <div class="checks" style="top:524px">
    <span><svg width="17" height="17"><use href="#tick"/></svg>Respektvoll &amp; individuell</span>
  </div>
</section>

<!-- Services -->
<section class="services">
  <article class="card" style="left:95px">
    <div class="badge"><svg width="30" height="30" viewBox="0 0 24 24" fill="none" stroke="#1a1d24" stroke-width="1.6" stroke-linejoin="round"><path d="M3 11l9-7 9 7v9H3z"/><path d="M12 17l-3-3a1.8 1.8 0 013-2 1.8 1.8 0 013 2z"/></svg></div>
    <h3>Hauskrankenpflege</h3>
    <p>Professionelle Pflege und Unterstützung in der vertrauten Umgebung Ihres eigenen Zuhauses.</p>
    <span class="more">Mehr erfahren →</span>
  </article>
  <article class="card outlined" style="left:351px">
    <div class="badge"><svg width="30" height="30" viewBox="0 0 24 24" fill="none" stroke="#1a1d24" stroke-width="1.6"><circle cx="6" cy="9" r="2.2"/><circle cx="12" cy="7" r="2.2"/><circle cx="18" cy="9" r="2.2"/><path d="M2.5 19v-3a3.5 3.5 0 017 0v3M8.5 19v-5a3.5 3.5 0 017 0v5M14.5 19v-3a3.5 3.5 0 017 0v3"/></svg></div>
    <h3>Tagespflege</h3>
    <p>Gemeinschaft erleben, aktiv bleiben und den Tag in guten Händen verbringen.</p>
    <span class="more">Mehr erfahren →</span>
  </article>
  <article class="card" style="left:607px">
    <div class="badge"><svg width="30" height="30" viewBox="0 0 24 24" fill="none" stroke="#1a1d24" stroke-width="1.6" stroke-linejoin="round"><path d="M12 20l-7.5-7.5a4.5 4.5 0 016.4-6.4L12 7.2l1.1-1.1a4.5 4.5 0 016.4 6.4z"/><path d="M8 13l3 2 5-5"/></svg></div>
    <h3>Individuelle Betreuung</h3>
    <p>Persönliche Unterstützung, abgestimmt auf Ihre Bedürfnisse, Möglichkeiten und Ihren Alltag.</p>
    <span class="more">Mehr erfahren →</span>
  </article>
  <article class="card" style="left:863px">
    <div class="badge"><svg width="30" height="30" viewBox="0 0 24 24" fill="none" stroke="#1a1d24" stroke-width="1.6"><circle cx="8.5" cy="7" r="2.6"/><circle cx="15.5" cy="7" r="2.6"/><path d="M4 20v-5a4 4 0 018 0v5M12 20v-5a4 4 0 018 0v5M12 11v9"/></svg></div>
    <h3>Entlastung Für Angehörige</h3>
    <p>Wir schaffen Sicherheit und Freiräume für Angehörige und pflegende Familienmitglieder.</p>
    <span class="more">Mehr erfahren →</span>
  </article>
</section>

<!-- Pflegeleitbild -->
<section class="leitbild">
  <h2 class="sec-title" style="left:95px;top:130px">Unser Pflegeleitbild</h2>
  <p class="body-text" style="left:95px;top:192px;width:500px">Wir, die Hauskranken- und Tagespflege „Am Lindenhof“,<br>sind ein unabhängiges, privatrechtliches Unternehmen der ambulanten bzw. teilstationären Kranken- und Seniorenpflege.</p>
  <p class="body-text" style="left:95px;top:268px;width:500px">Jeder Mensch hat den Wunsch mit Respekt und liebevoller Zuwendung versorgt zu werden. Das Ziel unserer Einrichtung ist unsere Betreuten bzw. ihre Angehörigen bei der Pflege und Bewältigung des Alltags im häuslichen Umfeld, in dieser Weise zu unterstützen. Somit kann eine Lebensführung und eine aktive Teilnahme an der Gesellschaft ermöglicht werden.</p>
  <a class="btn btn-yellow" style="left:95px;top:368px;width:182px"><svg class="ico" width="13" height="13"><use href="#phone"/></svg>0371 4470218</a>
  <a class="btn btn-white" style="left:279px;top:368px;width:182px">Mehr dazu erfahren</a>
  <div class="photo" role="img" aria-label="Zwei Hände halten sich vertrauensvoll" style="left:693px;top:81px;width:412px;height:388px;background:linear-gradient(135deg,#2f5f78 0%,#8aa9b8 40%,#d9a988 70%,#b98464 100%)"></div>
</section>

<!-- Hauskrankenpflege -->
<section style="top:1691px;height:560px">
  <div class="photo" role="img" aria-label="Pflegerin und Seniorin mit Gehstock in einer Küche" style="left:95px;top:93px;width:410px;height:387px;background:linear-gradient(135deg,#e7e5e1 0%,#c9cdd1 45%,#5f7f96 70%,#3d5e7a 100%)"></div>
  <h2 class="sec-title" style="left:553px;top:100px;width:520px">Hauskrankenpflege – Pflege Und Hilfe In Ihrem Zuhause</h2>
  <p class="body-text" style="left:553px;top:204px;width:500px">Lorem ipsum dolor sit amet consectetur. Sapien sit adipiscing mattis vestibulum. Tristique faucibus ipsum tellus nunc massa eu nisi sed. Lectus viverra sit volutpat id. Vel ac tristique lacus egestas velit sit. Lacus montes lectus sem bibendum amet.</p>
  <div class="feature-box" style="left:553px;top:285px;width:501px;height:109px">
    <h4>Unsere Leistungen</h4>
    <div class="feature-list">
      <span><svg width="13" height="13"><use href="#tick"/></svg>Rundumpflege</span>
      <span><svg width="13" height="13"><use href="#tick"/></svg>Hauswirtschaft</span>
      <span><svg width="13" height="13"><use href="#tick"/></svg>Durchführung ärztlicher Verordnungen</span>
      <span><svg width="13" height="13"><use href="#tick"/></svg>Vermittlung von Dienstleistungen</span>
    </div>
  </div>
  <a class="btn btn-yellow" style="left:553px;top:425px;width:166px">Mehr erfahren →</a>
</section>

<!-- Tagespflege -->
<section style="top:2251px;height:492px">
  <h2 class="sec-title" style="left:95px;top:20px;width:560px">Tagespflege – Betreuung In Geselliger Runde</h2>
  <p class="body-text" style="left:95px;top:124px;width:555px">Unsere Tagespflege bietet Platz für 18 Gäste. Der große Aufenthaltsraum mit offener Küche lädt zum gemütlichen Beisammensein ein. In unserem Ruheraum können sich unsere Gäste bei Bedarf zurückziehen und sich ausruhen, auch Therapien (Logopädie, Ergotherapie, Physiotherapie…) werden darin durchgeführt. Der Aufenthaltsraum ist zum Teil eingerichtet wie eine gemütliche Wohnstube, ihre Einrichtung erinnert an frühere Zeiten. Gemütliche Ruhesessel laden zum Entspannen ein.</p>
  <div class="feature-box" style="left:95px;top:243px;width:472px;height:75px">
    <div class="feature-list" style="grid-template-columns:280px 1fr">
      <span><svg width="13" height="13"><use href="#tick"/></svg>18 Gäste</span>
      <span><svg width="13" height="13"><use href="#tick"/></svg>Ruheraum</span>
      <span><svg width="13" height="13"><use href="#tick"/></svg>Großer Aufenthaltsraum Mit Offener Küche</span>
      <span><svg width="13" height="13"><use href="#tick"/></svg>Therapieangebote</span>
    </div>
  </div>
  <a class="btn btn-yellow" style="left:95px;top:346px;width:166px">Mehr erfahren →</a>
  <div class="photo" role="img" aria-label="Pflegerin begleitet eine Seniorin mit Gehstock" style="left:693px;top:16px;width:412px;height:382px;background:linear-gradient(135deg,#e7e5e1 0%,#c9cdd1 45%,#5f7f96 70%,#3d5e7a 100%)"></div>
</section>

<!-- Team -->
<section class="team">
  <h2>Hauskranken- Und Tagespflege „Am Lindenhof“ Unser Pflegeteam</h2>
  <p class="sub">Leitung Und Verwaltung</p>

  <article class="member" style="left:100px">
    <div class="ring"><div class="pic" role="img" aria-label="Porträt der Geschäftsführerin" style="background:linear-gradient(160deg,#d8c2b0,#a3473d)"></div></div>
    <div class="name">Renate Kühn</div>
    <div class="role">Geschäftsführerin</div>
    <ul><li>• Pflegedienstleitung</li><li>Hauskranken- und Tagespflege</li><li>• examinierte Krankenschwester</li></ul>
    <div class="go">→</div>
  </article>
  <article class="member" style="left:354px">
    <div class="ring"><div class="pic" role="img" aria-label="Porträt des Geschäftsführers" style="background:linear-gradient(160deg,#d9dde2,#2f4a6a)"></div></div>
    <div class="name">Jonas Kühn</div>
    <div class="role">Geschäftsführer / 2. Pflegedienstleitung</div>
    <ul><li>• Fortbildung PDL</li></ul>
    <div class="go">→</div>
  </article>
  <article class="member" style="left:608px">
    <div class="ring"><div class="pic" role="img" aria-label="Porträt der Pflegedienstleiterin" style="background:linear-gradient(160deg,#c8d6e2,#8fb4d4)"></div></div>
    <div class="name">Sabine Werner</div>
    <div class="role">1. Pflegedienstleitung</div>
    <ul><li>• Pflegedienstleitung</li><li>Hauskranken- und Tagespflege</li><li>• beschäftigt seit Januar 2014</li></ul>
    <div class="go">→</div>
  </article>
  <article class="member" style="left:862px">
    <div class="ring"><div class="pic" role="img" aria-label="Porträt der Leitung der Tagespflege" style="background:linear-gradient(160deg,#e8ebee,#2c3440)"></div></div>
    <div class="name">Lena Fischer</div>
    <div class="role">1. Pflegedienstleitung Tagespflege</div>
    <ul><li>• Fachkraft für Leitungsaufgaben</li><li>in Pflegeeinrichtungen</li><li>• Zusatzqualifikation:</li></ul>
    <div class="go">→</div>
  </article>

  <a class="btn btn-yellow" style="left:518px;top:661px;width:164px">Alle anzeigen →</a>
</section>

<!-- Contact -->
<section class="contact">
  <div class="form-box">
    <h2 class="sec-title" style="left:32px;top:50px">Kontaktieren Sie Uns</h2>
    <div class="field" style="left:30px;top:91px;width:306px;height:49px">Vorname</div>
    <div class="field" style="left:345px;top:91px;width:306px;height:49px">Nachname</div>
    <div class="field" style="left:30px;top:153px;width:306px;height:49px">E-Mail-Adresse</div>
    <div class="field" style="left:345px;top:153px;width:306px;height:49px">Telefonnummer</div>
    <div class="field" style="left:30px;top:213px;width:621px;height:190px;border-radius:16px;align-items:flex-start;padding-top:32px">Wie Können Wir Helfen?</div>
    <div class="abs" style="left:30px;top:434px;display:flex;align-items:center;gap:8px;font-size:11.5px;color:var(--text)">
      <svg width="13" height="13" viewBox="0 0 14 14"><rect x=".7" y=".7" width="12.6" height="12.6" rx="2" fill="none" stroke="#8a8f99"/><path d="M3.5 7l2.3 2.3L10.5 4.6" fill="none" stroke="#8a8f99" stroke-width="1.4"/></svg>
      Ich Stimme Der Datenschutzerklärung Und Den Nutzungsbedingungen Zu.
    </div>
    <a class="btn btn-yellow" style="left:492px;top:420px;width:159px">Jetzt senden →</a>
  </div>

  <aside class="hours">
    <h3>Öffnungszeiten</h3>
    <table>
      <tr><td>Monday</td><td>7:30AM - 5:00PM</td></tr>
      <tr><td>Tuesday</td><td>7:30AM - 5:00PM</td></tr>
      <tr><td>Wednesday</td><td>7:30AM - 5:00PM</td></tr>
      <tr><td>Thursday</td><td>7:30AM - 5:00PM</td></tr>
      <tr><td>Friday</td><td>7:30AM - 12:00PM</td></tr>
      <tr><td>Saturday</td><td>Closed</td></tr>
      <tr><td>Sunday</td><td>Closed</td></tr>
    </table>
    <div class="hour-rule"></div>
    <div class="cinfo" style="left:31px;top:338px"><div class="cicon"><svg width="14" height="14" fill="#fff"><use href="#phone"/></svg></div><span>24-hour hotline<br>0371 / 4470218</span></div>
    <div class="cinfo" style="left:31px;top:392px"><div class="cicon"><svg width="15" height="15"><use href="#mail"/></svg></div><span>Mon - Thurs: 9:00 - 15:00<br>Fri: 9:00 - 14:00<br>and by appointment</span></div>
    <div class="cinfo" style="left:31px;top:451px"><div class="cicon"><svg width="15" height="15"><use href="#pin"/></svg></div><span>Lindenallee 27<br>09130 Chemnitz</span></div>
  </aside>
</section>

<!-- Footer -->
<footer class="footer" style="position:absolute;left:0;width:1200px">
  <div class="foot-mark">Hauskranken- und<br>Tagespflege<br>„Am Lindenhof“</div>
  <div class="vrule" style="left:455px"></div>
  <div class="vrule" style="left:800px"></div>

  <div class="foot-col"><h3 style="left:574px">Links</h3></div>
  <ul class="foot-links">
    <li>Heim</li><li>Über uns</li><li>Team</li><li>Pflegeleitbild</li><li>Partner</li><li>Hauskrankenpflege</li><li>Tagespflege</li><li>Aktuelles</li>
  </ul>

  <div class="foot-col"><h3 style="left:918px">Kontakt</h3></div>
  <div class="cinfo" style="left:918px;top:132px"><div class="cicon"><svg width="14" height="14" fill="#fff"><use href="#phone"/></svg></div><span>24-hour hotline<br>0371 / 4470218</span></div>
  <div class="cinfo" style="left:918px;top:184px"><div class="cicon"><svg width="15" height="15"><use href="#mail"/></svg></div><span>Mon - Thurs: 9:00 - 15:00<br>Fri: 9:00 - 14:00<br>and by appointment</span></div>
  <div class="cinfo" style="left:918px;top:243px"><div class="cicon"><svg width="15" height="15"><use href="#pin"/></svg></div><span>Lindenallee 27<br>09130 Chemnitz</span></div>

  <div class="foot-bottom"></div>
  <p class="legal" style="left:95px">© 2026 Hauskranken- und Tagespflege „Am Lindenhof“</p>
  <p class="legal" style="right:95px">Kontakt · Datenschutz · Impressum · Erklärung Zur Barrierefreiheit</p>
</footer>

</body>
</html>
```